Construction business card

I need a new business card, they can connect with my logo, brand.
What we do is residential house , design and build
I like: Navy blue / black
I attached our logo, brand,
and, some idea for business card.

```html
<!DOCTYPE html>
<html lang="en">
<head>
<meta charset="utf-8">
<title>Harlow Ridge Builders – Business Card</title>
<link href="https://fonts.googleapis.com/css2?family=Arimo:wght@400;700&display=swap" rel="stylesheet">
<style>
  :root {
    --bg-top: #d4d4d4;
    --bg-bottom: #9e9e9e;
    --card: #262627;
    --card-deep: #1c1c1d;
    --blue: #3a86d4;
    --white: #f2f2f2;
    --emboss: #151516;
  }
  * { box-sizing: border-box; margin: 0; padding: 0; }
  html, body {
    width: 1200px; height: 802px; overflow: hidden;
    background: linear-gradient(180deg, var(--bg-top), var(--bg-bottom));
    font-family: "Arimo", Arial, sans-serif;
  }
  .card {
    position: absolute;
    width: 540px; height: 309px;
    background: var(--card);
    border-radius: 22px;
    border-bottom: 4px solid var(--blue);
    box-shadow: 0 18px 30px rgba(0,0,0,.35);
    color: var(--white);
  }
  .card--front { left: 50px; top: 120px; }
  .card--back { left: 610px; top: 380px; }

  .brand {
    position: absolute; left: 0; right: 0; top: 52px;
    display: flex; justify-content: center; align-items: center; gap: 10px;
    font-weight: 700; font-size: 24px; letter-spacing: .5px;
    color: var(--white);
  }
  .brand__mark { width: 14px; height: 14px; background: var(--blue); }

  .details {
    position: absolute; left: 0; right: 0; top: 138px;
    display: flex; justify-content: center; align-items: center;
  }
  .person { text-align: right; padding-right: 22px; }
  .person__name { color: var(--blue); font-weight: 700; font-size: 22px; letter-spacing: .5px; }
  .person__role { font-size: 15px; margin-top: 3px; }
  .divider { width: 1px; height: 62px; background: var(--blue); }
  .contacts { list-style: none; padding-left: 22px; font-size: 14px; line-height: 1.55; }
  .contacts li { display: flex; align-items: center; gap: 8px; }
  .contacts svg { width: 12px; height: 12px; fill: var(--blue); flex: none; }

  .address {
    position: absolute; left: 0; right: 0; bottom: 40px;
    text-align: center; font-size: 15px;
  }

  .brand--back {
    top: 50%; transform: translateY(-50%);
    font-size: 34px; color: var(--emboss);
  }
  .brand--back .brand__mark { width: 20px; height: 20px; background: var(--emboss); }
</style>
</head>
<body>
  <section class="card card--front">
    <div class="brand"><span class="brand__mark"></span>Harlow Ridge Builders</div>
    <div class="details">
      <div class="person">
        <p class="person__name">DANE WHITFORD</p>
        <p class="person__role">CEO/Founder</p>
      </div>
      <div class="divider"></div>
      <ul class="contacts">
        <li><svg viewBox="0 0 24 24" aria-hidden="true"><path d="M6.6 10.8a15 15 0 0 0 6.6 6.6l2.2-2.2c.3-.3.7-.4 1-.2 1.1.4 2.3.6 3.6.6.6 0 1 .4 1 1V20c0 .6-.4 1-1 1A17 17 0 0 1 3 4c0-.6.4-1 1-1h3.5c.6 0 1 .4 1 1 0 1.3.2 2.5.6 3.6.1.3 0 .7-.2 1z"/></svg>0400 555 018</li>
        <li><svg viewBox="0 0 24 24" aria-hidden="true"><path d="M2 5h20v14H2zm2 2v.5l8 5 8-5V7l-8 5z"/></svg>info@harlowridge.com.au</li>
        <li><svg viewBox="0 0 24 24" aria-hidden="true"><path d="M12 2a10 10 0 1 0 0 20 10 10 0 0 0 0-20zm6.9 9h-3a15 15 0 0 0-1.3-6 8 8 0 0 1 4.3 6zM12 4c.9 1.3 1.7 3.9 1.9 7h-3.8c.2-3.1 1-5.7 1.9-7zM9.4 5a15 15 0 0 0-1.3 6h-3a8 8 0 0 1 4.3-6zm-4.3 8h3a15 15 0 0 0 1.3 6 8 8 0 0 1-4.3-6zM12 20c-.9-1.3-1.7-3.9-1.9-7h3.8c-.2 3.1-1 5.7-1.9 7zm2.6-1a15 15 0 0 0 1.3-6h3a8 8 0 0 1-4.3 6z"/></svg>harlowridge.com.au</li>
      </ul>
    </div>
    <p class="address">27 Fernvale St, Oakridge, VIC 3100</p>
  </section>

  <section class="card card--back">
    <div class="brand brand--back"><span class="brand__mark"></span>Harlow Ridge Builders</div>
  </section>
</body>
</html>
```